Water Delivery Service Website

We are working with BrivoNessé. They are a water delivery company and in need of a new website design.
Some sites to use for inspiration:
https://www.pelmoriston.example/home
https://www.quintalbrook.example/en/home3
https://www.drevik.example
https://www.tormaxel.example
Thank you for taking the time to consider designing a website for us. We are web developers based in Stockton, CA, USA. Most of our projects go through the same process. Understanding this process may help you win a project with us. We custom-code all of our websites in-house. We don’t have any requirements as to what tools you use for your design, but we prefer Figma files. For any design that we label as four-stars, we send it to the client for review. The client picks the final design they want us to use. Once we complete this process, we will continue to show additional clients all the four-star sites and purchase them later. Your designs will have multiple chances to sell. For better chances of success, we ask that you follow these guidelines.
IMAGES:
If you use any images or icons in the design, we ask that you have a link to the asset so we can purchase the image/icon. Most of the designs we submit do not have the customer’s images on them unless they have some great images. Be creative; show us the feeling you are trying to portray with your image choices. Use any royalty-free site you choose. We subscribe to Vantrel and mainly use their images, but we can purchase images outside of Vantrel.
PLEASE NOTE: we will not submit designs to clients with watermarks on the images.
FONTS:
We ask that you identify the fonts used in the design. This can be done in a message if you want. We typically use Google Fonts and Vantrel Fonts.
CONTENT:
We're always open to different content and ideas. We often submit designs with stock images so the client can see our vision. We typically take pictures after the website launch to use their images with our vision. Lorem Ipsum is fine for paragraphs, but we ask that you write the headers in correct English. We want to be able to show the vision and identify the sections of the website.
INSPIRATION:
We typically add a couple of links in the brief of websites we like to help you get started in your design.
REVISIONS:
We do not often ask for revisions of the designs unless we see something in the design that may not appeal to the client. If there are slight changes that we want to make, we do that in the development process.
FEEDBACK:
We rarely give feedback on designs during the design process. We are working on many website projects and do not have the time to provide feedback. We usually respond if your request is well thought out and asks specific questions, but a note asking “feedback, please” usually goes unanswered.

```html
<!DOCTYPE html>
<html lang="en">
<head>
<meta charset="utf-8">
<title>BrivoNessé — Water Delivery</title>
<link href="https://fonts.googleapis.com/css2?family=Rubik:wght@400;500;600&family=Inter:wght@400;500;600;700&display=swap" rel="stylesheet">
<style>
:root{
  --navy:#1d1f5c;
  --blue:#1e8fd5;
  --sky:#2aa2e6;
  --ice:#eef6fc;
  --ice2:#dcecf8;
  --text:#3c3f55;
  --muted:#5b5e72;
  --white:#ffffff;
  --star:#ffd21f;
}
*{box-sizing:border-box;margin:0;padding:0}
html,body{width:1200px;height:4458px;overflow:hidden}
body{font-family:"Inter",sans-serif;color:var(--text);background:var(--white);position:relative}
.abs{position:absolute}
h1,h2,h3,h4{font-family:"Rubik",sans-serif;font-weight:500;color:#15162e}

/* header */
.site-header{position:absolute;top:0;left:0;width:1200px;height:86px;z-index:3}
.brand{position:absolute;display:flex;align-items:center;gap:8px;font-family:"Inter",sans-serif;font-weight:600;color:var(--navy)}
.brand .dot{width:16px;height:16px;border-radius:50%;background:var(--blue)}
.site-header .brand{left:110px;top:26px;font-size:26px}
.nav{position:absolute;left:446px;top:33px;display:flex;gap:34px;font-size:14px;color:#222}
.nav a{color:inherit;text-decoration:none}
.nav .active{color:var(--blue);font-weight:600;border-bottom:2px solid var(--blue);padding-bottom:3px}
.header-icons{position:absolute;left:874px;top:30px;display:flex;gap:16px}
.btn{display:inline-flex;align-items:center;justify-content:center;font-weight:600;font-size:15px;color:var(--white);border-radius:3px;text-decoration:none}
.btn-navy{background:var(--navy)}
.btn-blue{background:var(--sky)}
.contact-btn{position:absolute;left:957px;top:20px;width:131px;height:46px;font-size:16px}

/* hero */
.hero{position:absolute;top:0;left:0;width:1200px;height:600px;background:linear-gradient(180deg,#f4f9fd 0%,#e8f3fb 100%)}
.hero-welcome{position:absolute;left:110px;top:158px;font-size:31px;color:var(--sky);font-weight:500}
.hero-title{position:absolute;left:108px;top:222px;font-size:49px;line-height:58px;color:var(--navy)}
.hero-text{position:absolute;left:110px;top:348px;width:370px;font-size:14.5px;line-height:26px;color:#222}
.hero-actions{position:absolute;left:110px;top:443px;display:flex;gap:12px}
.hero-actions .btn{height:48px;padding:0 17px;font-size:15px}
.hero-swirl{position:absolute;left:560px;top:20px;width:640px;height:560px;border-radius:60% 0 0 40%;background:linear-gradient(160deg,#e6f1fa 0%,#d4e7f6 100%)}
.hero-media{position:absolute;left:535px;top:145px;width:660px;height:380px;border-radius:28px;background:linear-gradient(120deg,#cfe3f7 0%,#6f9fe4 30%,#3f73cf 50%,#8fb8ea 72%,#e2eef9 100%)}

/* section heads */
.sec-title{position:absolute;font-size:31px;text-align:center;left:0;width:1200px}
.squiggle{position:absolute;left:566px}

/* trusted */
.trusted-text{position:absolute;left:150px;top:778px;width:900px;text-align:center;font-size:14px;line-height:30px;color:#333}
.feature{position:absolute;top:870px;width:245px;text-align:center}
.feature .icon{width:100px;height:100px;border-radius:50%;background:var(--navy);margin:6px auto 0}
.feature .icon.light{background:var(--sky)}
.feature h3{font-size:19px;line-height:30px;margin-top:24px}
.feature p{font-size:14px;line-height:26px;color:var(--muted);margin-top:14px;padding:0 12px}
.feature .more{display:inline-flex;align-items:center;gap:8px;margin-top:24px;font-weight:600;font-size:15px;color:#111}
.divider{position:absolute;top:882px;width:1px;height:305px;background:#e2e6ee}

/* about */
.about{position:absolute;top:1250px;left:0;width:1200px;height:716px;background:linear-gradient(180deg,#eef6fc 0%,#f7fbfe 100%)}
.about-photo{position:absolute;left:147px;top:202px;width:400px;height:400px;border-radius:50%;border:3px solid var(--navy);padding:9px}
.about-photo div{width:100%;height:100%;border-radius:50%;background:linear-gradient(135deg,#5fa7dc,#c9a27b 60%,#8a6a52)}
.about-title{position:absolute;left:614px;top:175px;font-size:33px}
.about-text{position:absolute;left:614px;top:258px;width:476px;font-size:14px;line-height:28.5px;color:#333}
.about-text p+p{margin-top:28px}
.about-btn{position:absolute;left:614px;top:532px;width:132px;height:46px;font-size:15px}

/* protect */
.protect-person{position:absolute;left:470px;top:2200px;width:300px;height:438px;border-radius:30px 30px 0 0;background:linear-gradient(180deg,#eef3f8 0%,#e35345 25%,#d8332a 65%,#3b4d70 100%)}
.svc{position:absolute;width:278px;height:142px;background:var(--white);box-shadow:0 6px 24px rgba(30,50,90,.1);display:flex;align-items:center;gap:14px;padding:0 16px 0 24px}
.svc .txt{flex:1;text-align:center}
.svc h4{font-family:"Inter",sans-serif;font-weight:700;font-size:15px;color:var(--navy)}
.svc h4.blue{color:var(--sky)}
.svc p{font-size:13px;line-height:26px;color:var(--muted);margin-top:6px}
.svc .drop{width:62px;height:74px;flex:none}

/* testimonials */
.testi{position:absolute;top:2638px;left:0;width:1200px;height:640px}
.testi-title{position:absolute;top:125px;left:0;width:1200px;text-align:center;color:var(--white);font-size:31px;font-weight:600}
.t-card{position:absolute;top:265px;width:310px;height:187px;background:var(--white);border-radius:12px;box-shadow:0 8px 20px rgba(0,0,0,.12);text-align:center;padding:62px 22px 0;font-size:13.5px;line-height:26px;color:var(--muted)}
.avatar{position:absolute;top:217px;width:94px;height:94px;border-radius:50%;border:4px solid var(--white);background:linear-gradient(180deg,#c8d8e6,#7b96ad)}
.t-meta{position:absolute;top:480px;width:310px;display:flex;justify-content:center;gap:22px;color:var(--white);font-size:15px}
.stars{color:var(--star);letter-spacing:1px;font-size:14px}

/* blog */
.post{position:absolute;top:3465px;width:309px}
.post .thumb{height:242px}
.post .body{position:relative;margin:-28px 10px 0;background:var(--white);box-shadow:0 6px 22px rgba(20,30,60,.12);padding:24px 21px 24px;height:250px}
.badge{display:inline-block;background:var(--blue);color:var(--white);font-size:12px;font-weight:700;padding:7px 12px}
.post h3{font-family:"Inter",sans-serif;font-weight:700;font-size:14px;margin-top:22px;color:#111}
.post p{font-size:13.5px;line-height:26px;color:#444;margin-top:10px}
.read{display:inline-block;margin-top:22px;border:1.5px solid var(--navy);padding:10px 18px;font-size:12.5px;font-weight:700;color:var(--navy)}

/* footer */
.site-footer{position:absolute;top:4036px;left:0;width:1200px;height:422px;background:var(--navy);color:var(--white)}
.site-footer .brand{left:110px;top:130px;color:var(--white);font-size:40px;font-weight:500}
.site-footer .brand .dot{width:22px;height:22px;background:var(--white)}
.fcol{position:absolute;top:92px}
.fcol h4{color:var(--white);font-size:20px;font-weight:500}
.fcol ul{list-style:none;margin-top:14px}
.fcol li{font-size:14px;line-height:31px;display:flex;align-items:center;gap:12px}
.contact-item{display:flex;align-items:center;gap:14px;font-size:14px;height:36px;margin-top:24px}
.contact-item .circ{width:36px;height:36px;border-radius:50%;background:var(--white);display:flex;align-items:center;justify-content:center}
.rule{position:absolute;left:100px;top:364px;width:1000px;height:1px;background:rgba(255,255,255,.55)}
.copy{position:absolute;top:384px;left:0;width:1200px;text-align:center;font-size:13.5px}
</style>
</head>
<body>

<section class="hero">
  <div class="hero-swirl"></div>
  <svg class="abs" style="left:0;top:520px" width="1200" height="80" viewBox="0 0 1200 80"><path d="M0 50 Q600 110 1200 0 L1200 80 L0 80Z" fill="#fff"/></svg>
  <p class="hero-welcome">Welcome To</p>
  <svg class="abs" style="left:111px;top:205px" width="44" height="10" viewBox="0 0 44 10"><path d="M1 6 q5-6 10 0 t10 0 t10 0 t10 0" fill="none" stroke="#888" stroke-width="1.3"/></svg>
  <h1 class="hero-title">Pure And Healthy<br>Drinking Water</h1>
  <p class="hero-text">Lorem ipsum dolor sit amet, consectetur adipiscing elit, sed do eiusmod tempor incididunt ut labore et dolore magna aliqua.</p>
  <div class="hero-actions">
    <a class="btn btn-navy">Order Today!</a>
    <a class="btn btn-blue">Free Estimate</a>
  </div>
  <div class="hero-media" role="img" aria-label="Two large blue water cooler bottles with splashing water and ice cubes"></div>
</section>

<header class="site-header">
  <div class="brand"><span class="dot"></span>BrivoNessé</div>
  <nav class="nav">
    <a class="active">Home</a><a>About Us</a><a>Our Services</a><a>Our Products</a>
  </nav>
  <div class="header-icons">
    <svg width="20" height="20" viewBox="0 0 20 20" fill="none" stroke="#222" stroke-width="1.5"><circle cx="10" cy="6" r="4"/><path d="M2 19c0-5 4-7 8-7s8 2 8 7Z"/></svg>
    <svg width="22" height="20" viewBox="0 0 22 20" fill="none" stroke="#222" stroke-width="1.5"><path d="M1 2h3l3 11h11l2-8H6"/><circle cx="9" cy="17" r="1.5"/><circle cx="16" cy="17" r="1.5"/></svg>
  </div>
  <a class="btn btn-navy contact-btn">Contact Us</a>
</header>

<!-- trusted -->
<h2 class="sec-title" style="top:697px">Most Trusted Company</h2>
<svg class="squiggle" style="top:750px" width="68" height="12" viewBox="0 0 68 12"><path d="M1 7 q5-7 11 0 t11 0 t11 0 t11 0 t11 0 t11 0" fill="none" stroke="#2aa2e6" stroke-width="2"/></svg>
<p class="trusted-text">Lorem ipsum dolor sit amet, consectetur adipiscing elit, sed do eiusmod tempor incididunt ut labore et dolore magna aliqua. Ut enim ad minim veniam, quis nostrud exercitation ullamco laboris nisi ut aliquip ex ea commodo consequat.</p>

<div class="feature" style="left:92px"><div class="icon light"></div><h3>Soft Drinking<br>Water</h3><p>Excepteur sint occaecat cupidatat non proident, sunt in culpa qui officia</p><span class="more">View More <svg width="16" height="16" viewBox="0 0 16 16"><circle cx="8" cy="8" r="8" fill="#111"/><path d="M6 4l4 4-4 4" stroke="#fff" stroke-width="2" fill="none"/></svg></span></div>
<div class="divider" style="left:347px"></div>
<div class="feature" style="left:350px"><div class="icon"></div><h3>Cholorine Free<br>Water</h3><p>Excepteur sint occaecat cupidatat non proident, sunt in culpa qui officia</p><span class="more">View More <svg width="16" height="16" viewBox="0 0 16 16"><circle cx="8" cy="8" r="8" fill="#111"/><path d="M6 4l4 4-4 4" stroke="#fff" stroke-width="2" fill="none"/></svg></span></div>
<div class="divider" style="left:600px"></div>
<div class="feature" style="left:610px"><div class="icon"></div><h3>Pure Mineralized<br>Water</h3><p>Excepteur sint occaecat cupidatat non proident, sunt in culpa qui officia</p><span class="more">View More <svg width="16" height="16" viewBox="0 0 16 16"><circle cx="8" cy="8" r="8" fill="#111"/><path d="M6 4l4 4-4 4" stroke="#fff" stroke-width="2" fill="none"/></svg></span></div>
<div class="divider" style="left:860px"></div>
<div class="feature" style="left:868px"><div class="icon"></div><h3>Total Home<br>Solution</h3><p>Excepteur sint occaecat cupidatat non proident, sunt in culpa qui officia</p><span class="more">View More <svg width="16" height="16" viewBox="0 0 16 16"><circle cx="8" cy="8" r="8" fill="#111"/><path d="M6 4l4 4-4 4" stroke="#fff" stroke-width="2" fill="none"/></svg></span></div>

<!-- about -->
<section class="about">
  <svg class="abs" style="left:0;top:0" width="1200" height="90" viewBox="0 0 1200 90"><path d="M0 0 Q200 90 450 60 T1200 30 L1200 0Z" fill="#fff"/></svg>
  <div class="about-photo" role="img" aria-label="Delivery worker handing a large water bottle to a smiling customer at her door"><div></div></div>
  <h2 class="about-title">About Us</h2>
  <svg class="abs" style="left:614px;top:232px" width="66" height="12" viewBox="0 0 66 12"><path d="M1 7 q5-7 11 0 t11 0 t11 0 t11 0 t11 0" fill="none" stroke="#2aa2e6" stroke-width="2"/></svg>
  <div class="about-text">
    <p>Lorem ipsum dolor sit amet, consectetur adipiscing elit, sed do eiusmod tempor incididunt ut labore et dolore magna aliqua. Ut enim ad minim veniam, quis nostrud exercitation ullamco laboris nisi ut aliquip ex ea commodo consequat.</p>
    <p>Duis aute irure dolor in reprehenderit in voluptate velit esse cillum dolore eu fugiat nulla pariatur. Excepteur sint occaecat cupidatat non proident, sunt in culpa qui officia deserunt mollit anim id est laborum.</p>
  </div>
  <a class="btn btn-navy about-btn">Read More</a>
</section>

<!-- protect -->
<h2 class="sec-title" style="top:2085px;line-height:41px">Protect Your Family with Best Water<br>Filtering System Services</h2>
<svg class="squiggle" style="top:2180px" width="68" height="12" viewBox="0 0 68 12"><path d="M1 7 q5-7 11 0 t11 0 t11 0 t11 0 t11 0 t11 0" fill="none" stroke="#2aa2e6" stroke-width="2"/></svg>
<div class="protect-person" role="img" aria-label="Smiling delivery man in red cap and shirt carrying a water bottle on his shoulder"></div>
<div class="svc" style="left:155px;top:2208px"><div class="txt"><h4 class="blue">Residential Waters</h4><p>Lorem ipsum dolor sit amet adilit sed eiusmte</p></div><svg class="drop" viewBox="0 0 62 74"><path d="M31 2 C22 22 4 36 4 50 a27 24 0 0 0 54 0 C58 36 40 22 31 2Z" fill="#2aa2e6"/></svg></div>
<div class="svc" style="left:110px;top:2388px"><div class="txt"><h4>Soft Drink Waters</h4><p>Lorem ipsum dolor sit amet adilit sed eiusmte</p></div><svg class="drop" viewBox="0 0 62 74"><path d="M31 2 C22 22 4 36 4 50 a27 24 0 0 0 54 0 C58 36 40 22 31 2Z" fill="#1d1f5c"/></svg></div>
<div class="svc" style="left:755px;top:2208px"><div class="txt"><h4>Commercial Waters</h4><p>Lorem ipsum dolor sit amet adilit sed eiusmte</p></div><svg class="drop" viewBox="0 0 62 74"><path d="M31 2 C22 22 4 36 4 50 a27 24 0 0 0 54 0 C58 36 40 22 31 2Z" fill="#1d1f5c"/></svg></div>
<div class="svc" style="left:810px;top:2388px"><div class="txt"><h4 class="blue">Cholorine Water</h4><p>Lorem ipsum dolor sit amet adilit sed eiusmte</p></div><svg class="drop" viewBox="0 0 62 74"><path d="M31 2 C22 22 4 36 4 50 a27 24 0 0 0 54 0 C58 36 40 22 31 2Z" fill="#2aa2e6"/></svg></div>

<!-- testimonials -->
<section class="testi">
  <svg class="abs" style="left:0;top:0" width="1200" height="640" viewBox="0 0 1200 640"><path d="M0 0 H1200 V545 Q980 540 760 580 T0 630Z" fill="#1e8fd5"/></svg>
  <h2 class="testi-title">Client Testimonials</h2>
  <div class="t-card" style="left:110px">Sed ut perspiciatis unde omnis iste natus error sit voluptatem accusantium doloremque laudantium, totam rem aperiam, eaque ipsa</div>
  <div class="t-card" style="left:445px">Sed ut perspiciatis unde omnis iste natus error sit voluptatem accusantium doloremque laudantium, totam rem aperiam, eaque ipsa</div>
  <div class="t-card" style="left:778px">Sed ut perspiciatis unde omnis iste natus error sit voluptatem accusantium doloremque laudantium, totam rem aperiam, eaque ipsa</div>
  <div class="avatar" style="left:218px" role="img" aria-label="Client portrait"></div>
  <div class="avatar" style="left:553px" role="img" aria-label="Client portrait"></div>
  <div class="avatar" style="left:886px" role="img" aria-label="Client portrait"></div>
  <div class="t-meta" style="left:110px"><span>Tarin Vole</span><span class="stars">★★★★★</span></div>
  <div class="t-meta" style="left:445px"><span>Oskar Fenn</span><span class="stars">★★★★★</span></div>
  <div class="t-meta" style="left:778px"><span>Milo Rask</span><span class="stars">★★★★★</span></div>
</section>

<!-- blog -->
<h2 class="sec-title" style="top:3365px">Latest Blog</h2>
<svg class="squiggle" style="top:3418px" width="68" height="12" viewBox="0 0 68 12"><path d="M1 7 q5-7 11 0 t11 0 t11 0 t11 0 t11 0 t11 0" fill="none" stroke="#2aa2e6" stroke-width="2"/></svg>

<article class="post" style="left:110px"><div class="thumb" role="img" aria-label="Worker pushing a hand truck stacked with water bottles" style="background:linear-gradient(135deg,#7fb6e0,#d9e6ef 60%,#9aa5b0)"></div><div class="body"><span class="badge">OCT 05 2024</span><h3>LOREM IPSUM DOLOR SIT</h3><p>Excepteur sint occaecat cupidatat non proident, sunt in culpa qui officia deserunt mollit anim id est</p><span class="read">READ MORE</span></div></article>
<article class="post" style="left:445px"><div class="thumb" role="img" aria-label="Delivery man holding bottled water beside a van" style="background:linear-gradient(135deg,#3e4a5e,#6a7d94 50%,#a9c6e0)"></div><div class="body"><span class="badge">OCT 05 2024</span><h3>LOREM IPSUM DOLOR SIT</h3><p>Excepteur sint occaecat cupidatat non proident, sunt in culpa qui officia deserunt mollit anim id est</p><span class="read">READ MORE</span></div></article>
<article class="post" style="left:778px"><div class="thumb" role="img" aria-label="Smiling worker with rows of water bottles in a warehouse" style="background:linear-gradient(135deg,#5a4a3a,#a07a55 45%,#7fb3dc)"></div><div class="body"><span class="badge">OCT 05 2024</span><h3>LOREM IPSUM DOLOR SIT</h3><p>Excepteur sint occaecat cupidatat non proident, sunt in culpa qui officia deserunt mollit anim id est</p><span class="read">READ MORE</span></div></article>

<!-- footer -->
<footer class="site-footer">
  <div class="brand"><span class="dot"></span>BrivoNessé</div>
  <div class="fcol" style="left:386px"><h4>Quick Links</h4><ul>
    <li>➜ Home</li><li>➜ About Us</li><li>➜ Services</li><li>➜ Agriculture Trucking</li><li>➜ Contact Us</li></ul></div>
  <div class="fcol" style="left:620px"><h4>Other Links</h4><ul>
    <li>➜ FAQ</li><li>➜ Terms of Use</li><li>➜ Privacy Policy</li><li>➜ Support Links</li><li>➜ Conditions</li></ul></div>
  <div class="fcol" style="left:830px"><h4>Contact Us</h4>
    <div class="contact-item"><span class="circ"><svg width="14" height="16" viewBox="0 0 14 16"><path d="M7 0a6 6 0 0 0-6 6c0 4 6 10 6 10s6-6 6-10a6 6 0 0 0-6-6Z" fill="#1d1f5c"/><circle cx="7" cy="6" r="2" fill="#fff"/></svg></span>Company Name, United State.</div>
    <div class="contact-item"><span class="circ"><svg width="16" height="12" viewBox="0 0 16 12"><rect width="16" height="12" rx="1" fill="#1d1f5c"/><path d="M1 1l7 6 7-6" stroke="#fff" fill="none" stroke-width="1.3"/></svg></span>hello@brivonesse.example</div>
    <div class="contact-item"><span class="circ"><svg width="14" height="14" viewBox="0 0 14 14"><path d="M3 0l3 3-2 2a8 8 0 0 0 5 5l2-2 3 3-2 3C6 14 0 8 0 2Z" fill="#1d1f5c"/></svg></span>+1 555 014 2290</div>
  </div>
  <div class="rule"></div>
  <p class="copy">Copyrights@2025.Company Name.All Rights Reserved</p>
</footer>

</body>
</html>
```